Keystonery Billboard - Financial Services Company (Investments, Tax Planning and Insurance)

Our new office has a billboard directly above the office building. We'd like something eye-catching with a strong Call to Action, with the main part of the billboard being under 7 words if possible. We'd like you to include a way to get ahold of us (either our website keystoneryllc.example or our phone number 302-418-2907. You may also include in small font something to indicate that we've been serving the area since 1980 (the DE area, the tri-state area, the Marlowe Hollow, etc.)

We offer financial planning, tax planning, and insurance, and we help our clients to focus on their goals and happiness by providing everything they need for lifelong wealth under one roof.

Our logos are attached, we use a triangle logo with green and gray. We use the tagline "discover lasting prosperity" but this does not need to be included.

Potential ideas we have seen from other financial companies-
- the concept that the driver spends more time looking at billboards than planning for their retirement
-something along the lines of "everything you need for your finances is in this building right here" planning, investments, taxes, insurance"
-don't spend your time worrying about retirement, let us help you plan for it
-are you working for your money, or is it working for you?
- retirement takes planning, we're here to help
- ready to retire? talk to us
- need investment advice?
- need help investing?
- crossing your fingers isn't a retirement plan. we can help.
- retiring soon? you need help.

Those are just general ideas, please feel free to be creative.

brand colors:
#00b585
#00b185
#000000
#ffffff
#6d6f75
#6d6f75
#6f7074
#021712
#052e24

```html
<!DOCTYPE html>
<html lang="en">
<head>
<meta charset="utf-8">
<title>Keystonery Billboard</title>
<link rel="stylesheet" href="https://fonts.googleapis.com/css2?family=Oswald:wght@700&family=Montserrat:wght@700;800&family=Tinos:wght@700&display=swap">
<style>
  :root {
    --page-bg: #e6e6e7;
    --green-deep: #00432a;
    --green-mid: #1f7a50;
    --green-bright: #6ff5a8;
    --brand-green: #00b185;
    --arrow-green: #008a4f;
    --arrow-edge: #00b585;
    --bar-green: #024a2e;
    --gold: #ffe600;
    --white: #ffffff;
    --grey: #6d6f75;
  }
  html, body {
    margin: 0;
    width: 1000px;
    height: 1200px;
    overflow: hidden;
    background: var(--page-bg);
  }
  .billboard {
    position: absolute;
    left: 40px;
    top: 371px;
    width: 920px;
    height: 458px;
    display: block;
  }
  .headline { font-family: "Oswald", sans-serif; font-weight: 700; fill: var(--white); }
  .headline-accent { fill: var(--gold); }
  .brand-name { font-family: "Tinos", serif; font-weight: 700; fill: var(--brand-green); }
  .brand-tagline { font-family: "Montserrat", sans-serif; font-weight: 700; fill: var(--grey); letter-spacing: 4px; }
  .arrow-label { font-family: "Montserrat", sans-serif; font-weight: 800; fill: var(--white); }
  .services { font-family: "Tinos", serif; font-weight: 700; fill: var(--grey); }
  .services-divider { fill: var(--brand-green); }
  .contact { font-family: "Montserrat", sans-serif; font-weight: 800; fill: var(--white); }
</style>
</head>
<body>
<svg class="billboard" viewBox="0 0 1330 662" xmlns="http://www.w3.org/2000/svg" aria-label="Keystonery billboard">
  <defs>
    <linearGradient id="hero-gradient" x1="0" y1="0" x2="1" y2="0">
      <stop offset="0" stop-color="var(--green-deep)"/>
      <stop offset="0.35" stop-color="var(--green-mid)"/>
      <stop offset="1" stop-color="var(--green-bright)"/>
    </linearGradient>
    <linearGradient id="services-gradient" x1="0" y1="0" x2="0" y2="1">
      <stop offset="0" stop-color="#f4f4f4"/>
      <stop offset="1" stop-color="#e2e2e2"/>
    </linearGradient>
  </defs>

  <rect class="board-base" width="1330" height="662" fill="var(--white)"/>

  <!-- hero panel -->
  <polygon class="hero-panel" points="0,15 845,15 895,135 1330,135 1330,460 0,460" fill="url(#hero-gradient)"/>

  <!-- brand lockup -->
  <g class="brand-lockup">
    <rect x="932" y="44" width="34" height="34" fill="var(--brand-green)"/>
    <text class="brand-name" x="980" y="80" font-size="54">Keystonery</text>
    <text class="brand-tagline" x="1002" y="98" font-size="10.5">DISCOVER LASTING PROSPERITY</text>
  </g>

  <!-- headline -->
  <text class="headline" x="64" y="152" font-size="142" textLength="585" lengthAdjust="spacingAndGlyphs">WORRYING</text>
  <text class="headline" x="64" y="292" font-size="142" textLength="703" lengthAdjust="spacingAndGlyphs">ABOUT YOUR</text>
  <text class="headline" x="64" y="432" font-size="142" textLength="428" lengthAdjust="spacingAndGlyphs">MONEY?</text>
  <text class="headline headline-accent" x="510" y="432" font-size="142" textLength="425" lengthAdjust="spacingAndGlyphs">US TOO!</text>

  <!-- located here arrow -->
  <g class="location-arrow">
    <polygon points="1034,135 1276,135 1240,345 1298,345 1155,447 1012,345 1070,345"
             fill="var(--arrow-green)" stroke="var(--arrow-edge)" stroke-width="6" stroke-linejoin="miter"/>
    <text class="arrow-label" x="1155" y="193" font-size="33" text-anchor="middle">LOCATED</text>
    <text class="arrow-label" x="1155" y="236" font-size="33" text-anchor="middle">HERE</text>
    <g fill="none" stroke="var(--white)" stroke-width="12" stroke-linejoin="miter">
      <polyline points="1126,266 1155,288 1184,266"/>
      <polyline points="1126,296 1155,318 1184,296"/>
      <polyline points="1126,326 1155,348 1184,326"/>
      <polyline points="1126,356 1155,378 1184,356"/>
    </g>
  </g>

  <!-- services band -->
  <rect class="services-band" x="0" y="460" width="1330" height="105" fill="url(#services-gradient)"/>
  <text class="services" x="60" y="530" font-size="56" textLength="245" lengthAdjust="spacingAndGlyphs">Planning</text>
  <rect class="services-divider" x="336" y="498" width="4" height="36"/>
  <text class="services" x="370" y="535" font-size="56" textLength="332" lengthAdjust="spacingAndGlyphs">Investments</text>
  <rect class="services-divider" x="732" y="498" width="4" height="36"/>
  <text class="services" x="765" y="535" font-size="56" textLength="160" lengthAdjust="spacingAndGlyphs">Taxes</text>
  <rect class="services-divider" x="955" y="498" width="4" height="36"/>
  <text class="services" x="987" y="535" font-size="56" textLength="275" lengthAdjust="spacingAndGlyphs">Insurance</text>

  <!-- contact bar -->
  <rect class="contact-bar" x="0" y="565" width="1330" height="97" fill="var(--bar-green)"/>
  <g class="icon-phone">
    <circle cx="88" cy="615" r="28" fill="var(--white)"/>
    <path d="M76 600 l7 -3 l6 11 l-5 4 q4 9 12 13 l4 -5 l11 6 l-3 7 q-4 4 -10 2 q-18 -7 -25 -25 q-2 -6 3 -10 z" fill="var(--bar-green)"/>
  </g>
  <text class="contact" x="128" y="635" font-size="54" textLength="436" lengthAdjust="spacingAndGlyphs">302-418-2907</text>
  <rect x="592" y="592" width="4" height="46" fill="var(--white)"/>
  <g class="icon-globe">
    <circle cx="652" cy="615" r="28" fill="var(--white)"/>
    <g fill="none" stroke="var(--bar-green)" stroke-width="2.5">
      <circle cx="652" cy="615" r="17"/>
      <ellipse cx="652" cy="615" rx="7" ry="17"/>
      <line x1="635" y1="615" x2="669" y2="615"/>
      <line x1="638" y1="606" x2="666" y2="606"/>
      <line x1="638" y1="624" x2="666" y2="624"/>
    </g>
  </g>
  <text class="contact" x="697" y="635" font-size="54" textLength="566" lengthAdjust="spacingAndGlyphs">keystoneryllc.example</text>
</svg>
</body>
</html>
```